DESKHAVEN COSPACE Website design and coding

DESKHAVEN COSPACE

DESKHAVEN is Galveston’s first (and currently only) shared business co-working space. We share the same upscale, casual work environment, but we work independently on our own (or our team’s) projects and goals. For only a flat $195 membership fee per month, you have your very own all-inclusive, fun, personal business office environment. Website is written (Word file #12, below); and all pictures etc provided. Galveston is a beachy, coastal, historic city an hour from Houston, Texas USA. Logo (file 11 below) is temporary only.

Target Market(s)

Outside sales people, medical students looking for study hall, Houston companies looking for local office, real estate agents, graphic artists, entrepreneurs, etc

Contact Information for Business Card

will discuss --want to combine with current business card with multiple businesses

Logo Text

DESKHAVEN COSPACE

Coding

Coded - Design and coding required

Number of Pages Required

5+ page

Colors
ec1f27
fbed22

Requirements
Nice to have
• maroon/wine dominant with yellow and red accents, gray base are the colors of the space--website could coordinate--but open to creative ideas/combinations

```html
<!DOCTYPE html>
<html lang="en">
<head>
<meta charset="utf-8">
<title>DESKHAVEN COSPACE</title>
<link rel="stylesheet" href="https://fonts.googleapis.com/css2?family=Raleway:wght@300;400;500;600;700;800&display=swap">
<style>
:root{
  --red:#ec1f27;
  --yellow:#fbed22;
  --pale-yellow:#fefad6;
  --ink:#222;
  --body:#777;
  --white:#fff;
  --light:#f5f5f5;
  --footer:#232323;
  --footer-text:#9a9a9a;
}
*{margin:0;padding:0;box-sizing:border-box}
html,body{width:1200px;height:3644px;overflow:hidden}
body{font-family:"Raleway",sans-serif;color:var(--ink);background:var(--white);position:relative}
.abs{position:absolute}
.photo{position:absolute;display:block}
.btn{position:absolute;background:var(--red);color:var(--white);font-size:12.5px;font-weight:600;display:flex;align-items:center;justify-content:center;letter-spacing:.2px}

/* hero */
.hero{left:0;top:0;width:1200px;height:600px;background:linear-gradient(160deg,#4a4a4c 0%,#3b352c 35%,#5a4420 60%,#2a2620 100%)}
.hero-shade{left:0;top:0;width:1200px;height:600px;background:rgba(0,0,0,.35)}
.brand{color:var(--white);line-height:1}
.brand .name{font-size:24px;font-weight:800;letter-spacing:.5px}
.brand .sub{font-size:14px;font-weight:500;margin-top:3px}
.nav{top:27px;left:467px;width:640px;display:flex;justify-content:space-between;color:var(--white);font-size:11.5px;font-weight:500}
.hero-kicker{left:538px;top:238px;color:var(--white);font-size:19px;font-weight:400}
.hero-title{left:536px;top:262px;color:var(--yellow);font-size:58px;font-weight:800;letter-spacing:.5px}
.hero-sub{left:538px;top:328px;color:var(--white);font-size:25px;font-weight:500}

/* feature panels */
.panel-text{color:var(--white)}
.panel-text .kick{font-size:12px}
.panel-text .big{font-size:35px;font-weight:800;line-height:1.05;margin-top:2px}
.panel-text .line{font-size:11.5px;margin-top:3px}
.panel-text .more{font-size:12px;margin-top:24px;display:flex;align-items:center;gap:8px}

/* intro */
.kicker{font-size:19px;font-weight:400;color:#444}
.heading{font-size:40px;font-weight:800;color:var(--ink);line-height:1.1}
.para{font-size:14.5px;line-height:22.6px;color:var(--body);font-weight:400}

/* gallery */
.gallery{left:93px;top:1936px;width:1014px;height:377px;display:grid;grid-template-columns:repeat(4,1fr);grid-template-rows:1fr 1fr;gap:8px}
.gallery div{width:100%;height:100%}
.tall{grid-column:2;grid-row:1 / span 2}

/* testimonials */
.testimonials{left:0;top:2403px;width:1200px;height:545px;background:var(--light)}
.quote-card{left:548px;top:2561px;width:387px;height:319px;background:var(--white);box-shadow:0 2px 6px rgba(0,0,0,.08);padding:52px 24px 0 22px}
.quote-mark{color:var(--red);font-size:46px;font-weight:800;line-height:.6}
.quote-card p{font-size:12px;line-height:22.6px;color:var(--body);margin-top:20px}
.quote-card .who{font-size:13px;font-weight:600;margin-top:14px;color:var(--ink)}
.quote-card .role{font-size:10px;color:var(--body)}

/* services */
.service{position:absolute;top:3007px;width:300px;text-align:center}
.service .ring{width:98px;height:98px;margin:0 auto;border:5px solid var(--red);border-radius:50%;display:flex;align-items:center;justify-content:center}
.service h3{font-size:19px;font-weight:500;margin-top:25px;letter-spacing:.3px}
.service p{font-size:11.5px;color:var(--body);line-height:17px;margin-top:13px}
.service .more{font-size:12px;color:var(--red);font-weight:500;margin-top:15px}

/* footer */
.footer{left:0;top:3276px;width:1200px;height:368px;background:var(--footer)}
.f-col{position:absolute;top:3325px;color:var(--footer-text);font-size:11.5px;line-height:24px}
.f-col h4{color:var(--white);font-size:18px;font-weight:500;margin-bottom:12px;line-height:20px}
.f-col .text{line-height:17px}
.f-col a{color:var(--red);text-decoration:underline}
.contact-row{display:flex;gap:7px;line-height:15px;margin-bottom:26px}
.social{top:3535px;width:34px;height:34px;border:1px solid #555;border-radius:50%}
.copy{left:0;top:3581px;width:1200px;text-align:center;font-size:10px;color:#888}
.copy span{color:var(--yellow)}
</style>
</head>
<body>

<!-- hero -->
<div class="abs hero" role="img" aria-label="Coworking lounge with wooden tables, pendant lights and yellow chairs"></div>
<div class="abs hero-shade"></div>
<svg class="abs" style="left:360px;top:90px" width="420" height="420"><circle cx="210" cy="210" r="205" fill="none" stroke="rgba(255,255,255,.18)" stroke-width="1.5"/></svg>
<div class="abs brand" style="left:93px;top:16px"><div class="name">DESKHAVEN</div><div class="sub">COSPACE</div></div>
<nav class="abs nav"><span>ABOUT</span><span>AMENITIES</span><span>MEMBERSHIP</span><span>PICTURES</span><span>THE DESKHAVEN PHILOSOPHY</span><span>CONTACT</span></nav>
<div class="abs hero-kicker">DESKHAVEN IS</div>
<div class="abs hero-title">GALVESTON’S</div>
<div class="abs hero-sub">FIRST SHARED BUSINESS CO-WORKING SPACE</div>
<div class="btn" style="left:538px;top:375px;width:104px;height:37px">READ MORE</div>

<!-- panels -->
<div class="photo" style="left:0;top:600px;width:600px;height:337px;background:linear-gradient(135deg,#2c2c2c,#5b5a55 55%,#3a3a38)" role="img" aria-label="Office cubicles with yellow chairs and a plant"></div>
<div class="photo" style="left:600px;top:600px;width:600px;height:337px;background:linear-gradient(135deg,#3a3c36,#5a5e4e 50%,#6c6960)" role="img" aria-label="Kitchen corner with a large palm plant"></div>
<div class="abs panel-text" style="left:93px;top:796px">
  <div class="kick">Deskhaven Cospace</div><div class="big">AMENITIES</div>
  <div class="line">DESKHAVEN is the first Galveston co-working space</div>
  <div class="more">READ MORE <svg width="16" height="8"><path d="M0 4H14M10 1l4 3-4 3" stroke="#fff" fill="none" stroke-width="1.3"/></svg></div>
</div>
<div class="abs panel-text" style="left:822px;top:796px">
  <div class="kick">Deskhaven Cospace</div><div class="big">MEMBERSHIP</div>
  <div class="line">DESKHAVEN is the first Galveston co-working space</div>
  <div class="more">READ MORE <svg width="16" height="8"><path d="M0 4H14M10 1l4 3-4 3" stroke="#fff" fill="none" stroke-width="1.3"/></svg></div>
</div>

<!-- welcome -->
<div class="abs" style="left:531px;top:1054px;width:138px;height:665px;background:var(--pale-yellow)"></div>
<div class="abs kicker" style="left:93px;top:1050px">Welcome To</div>
<div class="abs heading" style="left:92px;top:1074px">DESKHAVEN COSPACE</div>
<p class="abs para" style="left:94px;top:1131px;width:465px">DESKHAVEN is Galveston’s first (and currently only) shared business co-working space. We share the same upscale, casual work environment, but we work independently on our own (or our team’s) projects and goals. For only a flat $195 membership fee per month, you have your very own all-inclusive, fun, personal business office environment.</p>
<div class="btn" style="left:93px;top:1283px;width:105px;height:37px">READ MORE</div>
<div class="photo" style="left:600px;top:1022px;width:507px;height:331px;background:linear-gradient(160deg,#d9d6cf,#7d776c 45%,#2d2b28)" role="img" aria-label="Lounge with black and white sofas, lockers and yellow chairs"></div>

<!-- philosophy -->
<div class="photo" style="left:95px;top:1426px;width:505px;height:333px;background:linear-gradient(150deg,#8a2433,#d8d4cc 45%,#2a2826)" role="img" aria-label="Red lockers beside a black leather sofa and glass door"></div>
<div class="abs kicker" style="left:644px;top:1465px">THE DESKHAVEN</div>
<div class="abs heading" style="left:643px;top:1488px">PHILOSOPHY</div>
<p class="abs para" style="left:645px;top:1545px;width:460px">Free yourself for the burdens of house or school, and work in an environment that MOTIVATES you instead of DISTRACTS you. Meet like-minded people that can help you along, and yet you have the option to work in a quiet-and very comfortable – private office cubicle.</p>
<div class="btn" style="left:644px;top:1678px;width:105px;height:37px">READ MORE</div>

<!-- gallery -->
<div class="abs kicker" style="left:0;top:1843px;width:1200px;text-align:center">PICTURE</div>
<div class="abs heading" style="left:0;top:1866px;width:1200px;text-align:center;font-size:38px">PHOTO GALLERY</div>
<div class="abs gallery">
  <div style="background:linear-gradient(160deg,#cfc9bb,#b58b3e 60%,#4a3a22)" role="img" aria-label="Long work tables under pendant lamps"></div>
  <div class="tall" style="background:linear-gradient(180deg,#e0dcd2,#a98a4f 55%,#3a2c1e)" role="img" aria-label="High table with stools under pendant lamps"></div>
  <div style="background:linear-gradient(160deg,#8a8d92,#c8c6bf 50%,#3c3a30)" role="img" aria-label="Cubicle row with yellow chairs"></div>
  <div style="background:linear-gradient(160deg,#d4d2cc,#9aa0a4 55%,#7a6a5a)" role="img" aria-label="Printer station and cubicles"></div>
  <div style="background:linear-gradient(160deg,#c9c6bf,#6b3a3c 45%,#2a2828)" role="img" aria-label="Lounge with sofas and lockers"></div>
  <div style="background:linear-gradient(160deg,#c8c8c4,#8e7a55 50%,#3c3226)" role="img" aria-label="Open workspace with tables and chairs"></div>
  <div style="background:linear-gradient(160deg,#b8b4aa,#8c8a7c 50%,#56684a)" role="img" aria-label="Glass office door with plants"></div>
</div>

<!-- testimonials -->
<div class="abs testimonials"></div>
<div class="abs kicker" style="left:93px;top:2465px">Testimonials</div>
<div class="abs heading" style="left:93px;top:2488px;font-size:38px">OUR CLIENT SAY’S</div>
<div class="photo" style="left:93px;top:2561px;width:159px;height:319px;background:var(--red)" role="img" aria-label="Portrait of a client in a suit, red tinted"></div>
<div class="photo" style="left:260px;top:2561px;width:285px;height:319px;background:linear-gradient(160deg,#33402e,#6b7a60 45%,#a9b8c8)" role="img" aria-label="Portrait of a smiling client in a light shirt"></div>
<div class="abs quote-card">
  <div class="quote-mark">“</div>
  <p>Sed ut perspiciatis unde omnis iste natus error sit voluptatem accusantium doloremque laudantium, totam rem aperiam, eaque ipsa quae ab illo inventore veritatis et quasi architecto beatae vitae dicta sunt explicabo.</p>
  <div class="who">Marlo Quenby</div>
  <div class="role">Consultant</div>
</div>
<div class="photo" style="left:947px;top:2561px;width:158px;height:319px;background:var(--red)" role="img" aria-label="Portrait of a client in a blazer, red tinted"></div>

<!-- services -->
<div class="service" style="left:113px">
  <div class="ring"><svg width="42" height="40" viewBox="0 0 42 40" fill="#222"><circle cx="21" cy="6" r="4"/><circle cx="9" cy="13" r="3.5"/><circle cx="33" cy="13" r="3.5"/><rect x="15" y="14" width="12" height="24"/><rect x="3" y="20" width="11" height="18"/><rect x="28" y="24" width="11" height="14"/></svg></div>
  <h3>COMPETITION</h3>
  <p>Because of the flexibility, prestigious location,<br>opportunities to meet and network...</p>
  <div class="more">READ MORE</div>
</div>
<div class="service" style="left:450px">
  <div class="ring"><svg width="44" height="38" viewBox="0 0 44 38" fill="#222"><circle cx="10" cy="8" r="5"/><circle cx="22" cy="6" r="5"/><circle cx="34" cy="8" r="5"/><rect x="4" y="15" width="36" height="6" rx="2"/><rect x="8" y="21" width="4" height="15"/><rect x="32" y="21" width="4" height="15"/></svg></div>
  <h3>COWORKERS</h3>
  <p>DESKHAVEN is a community– if you are making a<br>pot of (free) coffee...</p>
  <div class="more">READ MORE</div>
</div>
<div class="service" style="left:787px">
  <div class="ring"><svg width="42" height="40" viewBox="0 0 42 40"><circle cx="21" cy="7" r="5" fill="#222"/><circle cx="7" cy="28" r="4.5" fill="#222"/><circle cx="35" cy="28" r="4.5" fill="#222"/><path d="M13 22l6 6 10-12" stroke="#222" stroke-width="3.5" fill="none"/><path d="M2 39h38" stroke="#222" stroke-width="3"/></svg></div>
  <h3>YOUR SUCCESS</h3>
  <p>As your business grows, there are other<br>beautiful, “dedicated desk”...</p>
  <div class="more">READ MORE</div>
</div>

<!-- footer -->
<div class="abs footer"></div>
<div class="f-col" style="left:95px;width:300px">
  <h4>ABOUT US</h4>
  <div class="text">DESKHAVEN is Galveston’s first (and currently only) shared business co-working space. We share the same upscale, casual work environment...</div>
  <div style="margin-top:4px"><a>READ MORE</a></div>
</div>
<div class="abs brand" style="left:95px;top:3455px"><div class="name">DESKHAVEN</div><div class="sub">COSPACE</div></div>
<div class="f-col" style="left:463px">
  <h4>SITEMAP</h4>
  <div>About</div><div>Amenities</div><div>Membership</div><div>Pictures</div><div>The Deskhaven Philosophy</div><div>Contact</div>
</div>
<div class="f-col" style="left:696px">
  <h4>PHILOSOPHY</h4>
  <div>The Home</div><div>Competition</div><div>Coworkers</div><div>Your Success</div>
</div>
<div class="f-col" style="left:930px;width:180px">
  <h4>CONTACTS</h4>
  <div class="contact-row"><svg width="10" height="13" viewBox="0 0 10 13"><path d="M5 0a5 5 0 0 0-5 5c0 3.5 5 8 5 8s5-4.5 5-8a5 5 0 0 0-5-5z" fill="var(--yellow)"/><circle cx="5" cy="5" r="1.8" fill="#232323"/></svg><span>418 Harbor Ave, Ste. 12 Galveston, Tx 77550</span></div>
  <div class="contact-row"><svg width="10" height="12" viewBox="0 0 10 12"><path d="M2 0l2 3-1.3 1.5c.6 1.6 1.6 2.8 3 3.6L7 7l3 2-1 2.5C4 11 .5 6 0 1.5z" fill="var(--yellow)"/></svg><span>713-555-0148</span></div>
  <div class="contact-row"><svg width="12" height="9" viewBox="0 0 12 9"><rect width="12" height="9" fill="var(--yellow)"/><path d="M0 0l6 5 6-5" stroke="#232323" fill="none"/></svg><span>hello@deskhavenmail.com</span></div>
</div>
<div class="abs social" style="left:539px"></div>
<div class="abs social" style="left:583px"></div>
<div class="abs social" style="left:627px"></div>
<div class="abs copy">COPYRIGHT © 2020 <span>DESKHAVEN COSPACE</span>. ALL RIGHTS RESERVED.</div>

</body>
</html>
```